New bussiness card, using company logo.
Lionel Brisk
Manager/Director
Brisk Property Developments
Po Box 5347
Thuringowa Central
Qld
0491 638 205
lionel@briskpropertydevelopments
eye catching, vibrant colours, professional

```html
<!DOCTYPE html>
<html lang="en">
<head>
<meta charset="utf-8">
<title>Brisk Property Developments – Business Cards</title>
<link href="https://fonts.googleapis.com/css2?family=Open+Sans:wght@400;600;700&display=swap" rel="stylesheet">
<style>
  :root {
    --green: #6cbb45;
    --green-light: #8dc63f;
    --red: #e0262d;
    --ink: #333333;
    --white: #ffffff;
    --backdrop: #e9e6e3;
  }
  * { margin: 0; padding: 0; box-sizing: border-box; }
  html, body { width: 1200px; height: 746px; overflow: hidden; }
  body {
    position: relative;
    background: var(--backdrop);
    font-family: "Open Sans", Arial, sans-serif;
  }
  .card {
    position: absolute;
    width: 525px;
    height: 298px;
    overflow: hidden;
    box-shadow: 0 2px 6px rgba(0,0,0,.18);
  }
  .card--front { left: 45px; top: 35px; background: var(--white); }
  .card--back-white { left: 610px; top: 40px; background: var(--white); }
  .card--back-green { left: 47px; top: 395px; background: linear-gradient(180deg, var(--green) 0%, var(--green-light) 100%); }
  .card--back-red { left: 627px; top: 395px; background: var(--red); }

  .brand-name {
    position: absolute;
    font-weight: 700;
    line-height: 1.05;
    text-transform: uppercase;
    letter-spacing: .5px;
  }
  .brand-name--front {
    left: 30px; top: 62px;
    font-size: 27px;
    color: var(--red);
    width: 300px;
  }
  .brand-rule {
    position: absolute;
    left: 30px; top: 128px;
    width: 275px; height: 3px;
    background: var(--red);
  }
  .brand-mark {
    position: absolute;
    width: 14px; height: 14px;
    background: var(--green);
  }
  .brand-mark--front { left: 30px; top: 42px; }

  .contact-list {
    position: absolute;
    left: 28px; top: 174px;
    list-style: none;
    color: var(--ink);
  }
  .contact-item {
    display: flex;
    align-items: center;
    gap: 6px;
    font-size: 13px;
    margin-bottom: 9px;
  }
  .contact-item--email { font-size: 12px; }
  .contact-icon { width: 10px; height: 10px; flex: none; }

  .front-band {
    position: absolute;
    left: 0; right: 0; bottom: 0;
    height: 50px;
    background: linear-gradient(90deg, var(--red) 0%, var(--red) 30%, var(--green) 60%, var(--green) 100%);
  }
  .holder {
    position: absolute;
    right: 38px; bottom: 8px;
    text-align: right;
    color: var(--white);
  }
  .holder-name { font-size: 17px; font-weight: 700; line-height: 1.2; }
  .holder-role { font-size: 14px; line-height: 1.2; }

  .brand-name--centered {
    left: 0; right: 0;
    text-align: center;
    font-size: 34px;
  }
  .card--back-white .brand-name--centered { top: 118px; color: var(--green); }
  .card--back-green .brand-name--centered,
  .card--back-red .brand-name--centered { top: 120px; color: var(--white); }

  .website {
    position: absolute;
    left: 0; right: 0;
    text-align: center;
    font-size: 13px;
    letter-spacing: 3.2px;
  }
  .card--back-white .website { top: 252px; color: var(--ink); }
  .website-accent-red { color: var(--red); }
  .website-accent-green { color: var(--green); }
  .card--back-green .website,
  .card--back-red .website { top: 253px; color: var(--white); }
</style>
</head>
<body>

  <section class="card card--front" aria-label="Business card front">
    <span class="brand-mark brand-mark--front"></span>
    <div class="brand-name brand-name--front">Brisk Property<br>Developments</div>
    <div class="brand-rule"></div>

    <ul class="contact-list">
      <li class="contact-item">
        <svg class="contact-icon" viewBox="0 0 10 10"><path d="M5 0.5 L10 5 H8.5 V9.5 H6 V6.5 H4 V9.5 H1.5 V5 H0 Z" fill="#e0262d"/></svg>
        Po Box 5347, Thuringowa Central , Qld
      </li>
      <li class="contact-item">
        <svg class="contact-icon" viewBox="0 0 10 10"><path d="M2 0.5 L3.8 2.6 L2.8 3.8 C3.5 5.3 4.7 6.5 6.2 7.2 L7.4 6.2 L9.5 8 L8.2 9.5 C4.3 9 1 5.7 0.5 1.8 Z" fill="#e0262d"/></svg>
        0491 638 205
      </li>
      <li class="contact-item contact-item--email">
        <svg class="contact-icon" viewBox="0 0 10 10"><rect x="0" y="2" width="10" height="6.5" fill="#e0262d"/><path d="M0 2 L5 5.5 L10 2" stroke="#fff" stroke-width="1" fill="none"/></svg>
        lionel@briskpropertydevelopments.com
      </li>
    </ul>

    <div class="front-band" role="img" aria-label="Decorative red and green wave band"></div>

    <div class="holder">
      <div class="holder-name">Lionel Brisk</div>
      <div class="holder-role">Manager/Director</div>
    </div>
  </section>

  <section class="card card--back-white" aria-label="Business card back, white">
    <div class="brand-name brand-name--centered">Brisk Property Developments</div>
    <div class="website">www.<span class="website-accent-red">brisk</span><span class="website-accent-green">propertydevelopments</span>.com</div>
  </section>

  <section class="card card--back-green" aria-label="Business card back, green">
    <div class="brand-name brand-name--centered">Brisk Property Developments</div>
    <div class="website">www.briskpropertydevelopments.com</div>
  </section>

  <section class="card card--back-red" aria-label="Business card back, red">
    <div class="brand-name brand-name--centered">Brisk Property Developments</div>
    <div class="website">www.briskpropertydevelopments.com</div>
  </section>

</body>
</html>
```